tallow-brook.com

We are a small dollar lending company that will revolutionize the industry. We will do this by being completely transparent, fee free, etc and an interest rate that normal people can afford to pay. Over 10X less than our competition. We only allow our members to pay bills " bills paid fast", within 72 hours. Payday loans typically charge from 390%-600% with a terrible payback structure. We charge 36%, period, with a payback structure over 12 months. Our site will be very simple and easy to use but elegant at the same time. We do not want the site to be too busy, less is more and easier. We will have; Home, The Story, Why tallowbrook.com, Are you eligible? Members, Clients. To become a member you have to be referred by a current client of tallowbrook.com. A lot of the busy stuff will be saved for the Members and Clients sections. The feel must be elegant, easy to use and very simple to understand. I am looking for the green, white and black combinations of colors, very similar to my logo that was designed by Fernquillo.

```html
<!DOCTYPE html>
<html lang="en">
<head>
<meta charset="utf-8">
<title>Tallow Brook – Small Dollar Lending</title>
<link href="https://fonts.googleapis.com/css2?family=Montserrat:ital,wght@0,300;0,400;0,600;0,700;1,700&family=Open+Sans:wght@400;600;700&display=swap" rel="stylesheet">
<style>
:root{
  --green:#83bd3e;
  --green-light:#9ccd55;
  --green-deep:#4a9415;
  --green-dark:#1e3d06;
  --green-head:#3f8c10;
  --ink:#111;
  --text:#3a3a3a;
  --white:#fff;
  --page:#fff;
}
*{box-sizing:border-box;margin:0;padding:0}
html,body{width:1065px;height:1200px;overflow:hidden;background:var(--page)}
body{font-family:"Montserrat",sans-serif;color:var(--text);position:relative}
.wrap{position:absolute;left:115px;width:834px}

.brand{position:absolute;left:115px;top:13px;width:200px;height:107px;display:flex;align-items:center;gap:10px}
.brand-dot{width:42px;height:42px;border-radius:50%;background:var(--green)}
.brand-name{font-family:"Montserrat",sans-serif;font-weight:400;font-size:26px;color:var(--ink);letter-spacing:.5px}
.signin{position:absolute;left:858px;top:90px;width:90px;height:31px;background:#3b3b3b;border:1px solid #222;color:var(--white);font-family:"Open Sans",sans-serif;font-weight:600;font-size:13px;display:flex;align-items:center;justify-content:center}

.nav{top:130px;height:55px;background:linear-gradient(var(--green-light),var(--green));display:flex;align-items:center;padding-left:30px}
.nav a{font-family:"Open Sans",sans-serif;font-weight:700;font-size:15.5px;color:var(--white);text-decoration:none;margin-right:29px}
.nav a.current{color:var(--ink)}
.search{position:absolute;right:10px;top:17px;width:160px;height:21px;background:var(--white);border:1px solid #ccc;font-family:"Open Sans",sans-serif;font-size:10.5px;color:#999;padding:3px 7px}
.search svg{position:absolute;right:4px;top:4px}

.hero{top:185px;height:343px;background:
  linear-gradient(90deg,rgba(0,0,0,0) 40%,rgba(0,0,0,.55) 100%),
  linear-gradient(90deg,#d8d7d4 0%,#c9c6c0 20%,#d9975a 35%,#c98a4a 55%,#6e5440 75%,#2d2a27 100%)}
.hero-copy{position:absolute;right:40px;top:220px;text-align:right;font-family:"Montserrat",sans-serif;font-weight:700;font-size:18px;line-height:26px;color:var(--white)}
.hero-copy .tag{color:var(--green);font-size:21px;display:block;margin-top:1px}
.hero-arrows{position:absolute;right:42px;top:320px;display:flex;gap:8px}

.welcome{top:560px;width:548px}
h2{font-family:"Montserrat",sans-serif;font-weight:600;font-size:21px;color:var(--green-head);letter-spacing:.2px}
p{font-weight:300;font-size:12.6px;line-height:21.3px;color:var(--text)}
.welcome h2{margin-bottom:14px}
.welcome p+p{margin-top:10px}

.lend{position:absolute;left:683px;top:549px;width:266px;height:270px;background:var(--green-deep);padding:18px 12px}
.lend h3{font-family:"Montserrat",sans-serif;font-style:italic;font-weight:700;font-size:16px;color:var(--white);margin-bottom:12px}
.field{height:36px;background:var(--green-dark);color:var(--white);font-size:11.5px;display:flex;align-items:center;justify-content:space-between;padding:0 8px;margin-bottom:11px}
.submit{width:99px;height:35px;background:#000;color:var(--white);font-weight:700;font-size:12px;letter-spacing:.5px;display:flex;align-items:center;justify-content:center;margin-top:-1px}
.terms{display:flex;align-items:center;gap:8px;color:var(--white);font-size:11.5px;margin-top:9px}
.box{width:11px;height:11px;background:var(--white);border:1px solid #777;display:flex;align-items:center;justify-content:center}

.col{position:absolute;top:855px;width:270px}
.col h2{margin-bottom:24px}
.col p{padding-left:2px}
.person{font-weight:700;font-size:13px;color:var(--green-head);margin-top:8px;padding-left:6px}
.company{font-size:10px;color:var(--text);padding-left:6px;margin-top:4px}
.more{position:absolute;top:1047px;width:103px;height:38px;background:var(--green-deep);color:var(--white);font-weight:600;font-size:13px;display:flex;align-items:center;justify-content:center}

.footer{position:absolute;left:0;top:1126px;width:1065px;height:74px;background:var(--green-deep)}
.foot-links{position:absolute;left:117px;top:13px;font-family:"Open Sans",sans-serif;font-size:13px;color:var(--white);display:flex}
.foot-links span.sep{margin:0 19px}
.copy{position:absolute;left:117px;top:47px;font-family:"Open Sans",sans-serif;font-size:13px;color:var(--white)}
.social{position:absolute;left:772px;top:20px;display:flex;gap:12px}
.social span{width:29px;height:29px;border-radius:50%;background:#111}
</style>
</head>
<body>

<div class="brand"><span class="brand-dot"></span><span class="brand-name">Tallow Brook</span></div>
<div class="signin">Sigin In</div>

<nav class="wrap nav">
  <a class="current">Home</a><a>The Story</a><a>Why tallowbrook.com</a><a>Are you eligible?</a><a>Members</a><a>Clients</a>
  <div class="search">Search
    <svg width="10" height="10" viewBox="0 0 10 10"><circle cx="4" cy="4" r="3" fill="none" stroke="#bbb" stroke-width="1.3"/><line x1="6.2" y1="6.2" x2="9" y2="9" stroke="#bbb" stroke-width="1.5"/></svg>
  </div>
</nav>

<section class="wrap hero" role="img" aria-label="Photo of a smiling businessman in a suit with colleagues talking in a bright office behind him">
  <div class="hero-copy">With the money we lend we will<br>allow people only to pay bills.<span class="tag">" Bills Paid Fast "</span></div>
  <div class="hero-arrows">
    <svg width="16" height="24" viewBox="0 0 16 24"><polyline points="13,2 3,12 13,22" fill="none" stroke="#fff" stroke-width="3"/></svg>
    <svg width="16" height="24" viewBox="0 0 16 24"><polyline points="3,2 13,12 3,22" fill="none" stroke="#fff" stroke-width="3"/></svg>
  </div>
</section>

<section class="wrap welcome">
  <h2>Welcome to Tallow Brook</h2>
  <p>Lorem Ipsum is simply dummy text of the printing and typesetting industry. Lorem Ipsum has been the industry's standard dummy text ever since the 1500s, when an unknown printer took a galley of type and scrambled it to make a type specimen book. It has survived not only five centuries, but also the leap into electronic typesetting, remaining essentially unchanged. It was popularised in the 1960s with the release of Lettrex sheets containing Lorem Ipsum passages, and more recently with desktop publishing software like Pagewright including versions of Lorem Ipsum.</p>
  <p>&nbsp;It was popularised in the 1960s with the release of Lettrex sheets containing Lorem Ipsum passages, and more recently with desktop publishing software like Pagewright including versions of Lorem Ipsum.</p>
</section>

<aside class="lend">
  <h3>Small Dollar’s Lending</h3>
  <div class="field">How much do you need</div>
  <div class="field">What is it for ?
    <svg width="16" height="10" viewBox="0 0 16 10"><polyline points="2,2 8,8 14,2" fill="none" stroke="#fff" stroke-width="2.2"/></svg></div>
  <div class="field">How much is your credit
    <svg width="16" height="10" viewBox="0 0 16 10"><polyline points="2,2 8,8 14,2" fill="none" stroke="#fff" stroke-width="2.2"/></svg></div>
  <div class="submit">SUBMIT</div>
  <div class="terms"><span class="box"><svg width="9" height="9" viewBox="0 0 9 9"><polyline points="1,4.5 3.5,7 8,1.5" fill="none" stroke="#2a5bb0" stroke-width="1.8"/></svg></span>Accept the terms &amp; conditions</div>
</aside>

<section class="col" style="left:115px">
  <h2>Who We are ?</h2>
  <p>We are a small dollar lending company, We will do this by being completely transparent, fee free, etc and an interest rate that normal people can afford to pay. Over 10X less than our competition.</p>
</section>
<section class="col" style="left:398px">
  <h2>Why choose Us ?</h2>
  <p>We charge only 36% and give over 12 months time to pay back, no fees, hidden costs etc.</p>
</section>
<section class="col" style="left:683px">
  <h2>Testimonials</h2>
  <p>Lorem Ipsum is simply dummy text of the printing and typesetting industry. Lorem Ipsum has been the industry's standard dummy text ever since the 1500s</p>
  <div class="person">Dana Whitcombe</div>
  <div class="company">Company name</div>
</section>

<div class="more" style="left:115px">Read More</div>
<div class="more" style="left:400px">Read More</div>
<div class="more" style="left:683px">Read More</div>

<footer class="footer">
  <div class="foot-links">
    <span>Home</span><span class="sep">|</span><span>The Story</span><span class="sep">|</span><span>Why tallowbrook.com</span><span class="sep">|</span><span>Are you eligible?</span><span class="sep">|</span><span>Members</span><span class="sep">|</span><span>Clients</span>
  </div>
  <div class="copy">© 2014 Company Name ,All Rights Reserved</div>
  <div class="social" aria-label="Social media links">
    <span></span><span></span><span></span><span></span><span></span>
  </div>
</footer>

</body>
</html>
```